Hello Creative Minds!
Our business is after a elegant and classy flyer that draws attention!
The business is Velvet Turf - Lawn Revival Services. We provide services that maintain a healthy and vibrant green lawn through the tough Australian seasons. The products we use limits the water needed to keep grass green to a minimum - practically none at all! This not only helps the home owner or home seller but the environment by limiting the use of water that is needed to create a green lawn. The products we use are made from natural ingredients that are and pet friendly.
This fly will be our introductory offer to the market. Below are the required points that need to be on the flyer. Attached is the business logo, before & after pictures and 1 example of the LAYOUT not DESIGN of what the flyer should be laid out like or similar to. Feel free to use different 'Lawn Mower' pictures.
All the best; if you need any questions answered please feel free to message.
REQUIRED POINTS (Please re-phrase were possible);
*Instantly restores the natural green colour of grass – year round
*Lasts for up to 3 months
*Substantially reduces watering needs
*Pet friendly
*Stays green during droughts and water restrictions
*UV fade resistant
*Won’t bleed, run, or stain once absorbed into the grass
*Safe for the environment, pets and people
*Works in extreme heat, cold and frost
*Organic and natural – no harmful chemicals
*Reduces the amount of fertilizer
and water used on lawns
*Kerb appeal is essential for getting your property sold for the highest price possible
SERVICES & PRICING
Lawn maintenance (cut & trim) starting from $60
Lawn rejuvenation starting from $80 (Only $27 a month for 3 months)*
Package deal starting from $120
Introductory offer: 25% off all services. Refer a friend, when they book you receive another 25% off your next service.
LOCATIONS
Nowra to Sydney
CONTACT NUMBER
Will be posted with the winner - please leave an area for this.
SOCIAL MEDIA
Please add Chatterbook and Snapgrid logo's
Updates
Target Market(s)
home owners, home sellers, property developers, real estates and nursing homes and government housing.
Industry/Entity Type
Lawn Care
Look and feel
Each slider illustrates characteristics of the customer's brand and the style your logo design should communicate.

```html
<!DOCTYPE html>
<html lang="en">
<head>
<meta charset="utf-8">
<title>Velvet Turf – Lawn Revival Services Flyer</title>
<link rel="stylesheet" href="https://fonts.googleapis.com/css2?family=Yellowtail&family=Montserrat:wght@500;600;700;800&family=Lato:wght@400;700&display=swap">
<style>
  :root {
    --page-bg: #dcdcdc;
    --flyer-bg: #262b33;
    --flyer-bg-low: #2d323a;
    --line: #d8dadc;
    --lime: #d6e23c;
    --leaf: #7fb540;
    --text: #eef0f2;
    --offer-red: #d3202a;
    --white: #ffffff;
  }
  * { box-sizing: border-box; margin: 0; padding: 0; }
  html, body { width: 1200px; height: 920px; overflow: hidden; background: var(--page-bg); }
  .flyer {
    position: absolute; left: 280px; top: 20px; width: 640px; height: 880px;
    background: linear-gradient(180deg, var(--flyer-bg) 0%, var(--flyer-bg) 70%, var(--flyer-bg-low) 100%);
    color: var(--text); font-family: "Lato", sans-serif; overflow: hidden;
    box-shadow: 0 10px 30px rgba(0,0,0,.35);
  }
  .headline {
    position: absolute; left: 36px; top: 30px; width: 580px;
    font-family: "Yellowtail", cursive; font-weight: 400; font-size: 74px; line-height: 62px;
    background: linear-gradient(90deg, var(--lime) 0%, #b6cd3e 50%, var(--leaf) 100%);
    -webkit-background-clip: text; background-clip: text; color: transparent;
    z-index: 5;
    filter: drop-shadow(2px 3px 2px rgba(0,0,0,.6));
  }
  .headline .line-two { display: block; padding-left: 180px; }
  .photo-frame {
    position: absolute; left: 150px; top: 128px; width: 380px; height: 382px;
    border: 1.5px solid var(--line);
  }
  .photo { position: absolute; left: 6px; width: 366px; }
  .photo-before { top: 4px; height: 176px;
    background: linear-gradient(180deg, #8f9499 0%, #9aa0a3 35%, #a0b865 55%, #7d848a 80%, #6d7378 100%); }
  .photo-after { top: 188px; height: 186px;
    background: linear-gradient(180deg, #8a9095 0%, #959b9f 35%, #5fb43a 55%, #777d82 80%, #676d72 100%); }
  .swatch {
    position: absolute; width: 140px; height: 140px; border-radius: 50%;
    border: 3px solid var(--white); box-shadow: 0 4px 10px rgba(0,0,0,.5);
  }
  .swatch-before { left: 75px; top: 115px;
    background: radial-gradient(circle at 40% 40%, #cdb88d 0%, #a89066 60%, #7e6c4c 100%); }
  .swatch-after { left: 427px; top: 238px;
    background: radial-gradient(circle at 40% 40%, #6fae3d 0%, #3f8526 60%, #2c5e1b 100%); }
  .swatch-labels { position: absolute; left: 0; top: 0; width: 640px; height: 880px; pointer-events: none; }
  .swatch-labels text { font-family: "Montserrat", sans-serif; font-weight: 700; font-size: 14px; letter-spacing: 4px; fill: var(--white); }
  .offer {
    position: absolute; left: 44px; top: 275px; width: 232px; height: 96px;
    transform: rotate(-3deg); z-index: 6;
  }
  .offer svg { position: absolute; inset: 0; }
  .offer-copy { position: relative; text-align: center; padding: 6px 24px 0 6px; font-family: "Montserrat", sans-serif; color: var(--white); }
  .offer-title { font-weight: 700; font-size: 13.5px; line-height: 16px; }
  .offer-figure { font-weight: 800; font-size: 29px; line-height: 28px; }
  .offer-scope { font-weight: 700; font-size: 13.5px; line-height: 16px; }
  .offer-refer { font-weight: 700; font-size: 8px; line-height: 10px; margin-top: 4px; }
  .panel { position: absolute; border: 1.5px solid var(--line); }
  .panel-title {
    position: absolute; top: -9px; background: var(--flyer-bg); padding: 0 5px;
    font-family: "Montserrat", sans-serif; font-weight: 700; font-size: 12.5px; line-height: 16px; color: var(--white); letter-spacing: .3px;
  }
  .benefits { left: 62px; top: 548px; width: 370px; height: 186px; }
  .benefits .panel-title { left: 118px; }
  .benefit-cols { display: flex; gap: 12px; padding: 16px 10px 0 14px; }
  .benefit-list { list-style: none; flex: 1; font-size: 9.5px; line-height: 11.5px; }
  .benefit-list li { position: relative; padding-left: 10px; margin-bottom: 4px; }
  .benefit-list li::before { content: "✓"; position: absolute; left: 0; top: 0; color: var(--lime); font-weight: 700; }
  .pricing { left: 440px; top: 536px; width: 180px; height: 180px; padding: 16px 12px 0 16px; }
  .pricing .panel-title { left: 22px; }
  .price-item { margin-bottom: 9px; }
  .price-name { font-family: "Montserrat", sans-serif; font-weight: 700; font-size: 10.5px; color: var(--lime); letter-spacing: .2px; }
  .price-line { font-size: 9.5px; }
  .price-line strong { font-size: 13px; font-weight: 700; color: var(--white); }
  .brand {
    position: absolute; left: 130px; top: 762px; width: 300px; text-align: center;
    font-family: "Lato", sans-serif; font-weight: 700; font-size: 40px; color: var(--white);
  }
  .contacts { position: absolute; left: 480px; top: 748px; list-style: none; font-size: 9.5px; }
  .contacts li { display: flex; align-items: center; gap: 8px; height: 26px; margin-bottom: 8px; }
  .contact-chip { width: 26px; height: 26px; background: var(--lime); border-radius: 3px; flex: none; }
  .call {
    position: absolute; left: 94px; top: 838px;
    font-family: "Montserrat", sans-serif; font-weight: 700; font-size: 19px; color: var(--white); letter-spacing: .8px;
  }
  .call .phone { color: var(--leaf); font-size: 27px; letter-spacing: 2px; margin-left: 8px; }
</style>
</head>
<body>
<main class="flyer">
  <h1 class="headline">Make your lawn <span class="line-two">great again!</span></h1>

  <div class="photo-frame">
    <div class="photo photo-before" role="img" aria-label="Backyard lawn before treatment, patchy grass beside a paved patio and fence"></div>
    <div class="photo photo-after" role="img" aria-label="Same backyard lawn after treatment, vivid green grass beside the patio"></div>
  </div>

  <div class="swatch swatch-before" role="img" aria-label="Close-up of dry straw-coloured grass"></div>
  <div class="swatch swatch-after" role="img" aria-label="Close-up of lush green grass"></div>

  <svg class="swatch-labels" viewBox="0 0 640 880" aria-hidden="true">
    <defs>
      <path id="arc-before" d="M 72 235 A 88 88 0 0 1 118 101"/>
      <path id="arc-after" d="M 474 223 A 88 88 0 0 1 585 308"/>
    </defs>
    <text><textPath href="#arc-before">BEFORE</textPath></text>
    <text><textPath href="#arc-after">AFTER</textPath></text>
  </svg>

  <div class="offer">
    <svg viewBox="0 0 232 96" preserveAspectRatio="none" aria-hidden="true">
      <polygon points="0,0 214,0 232,48 214,96 0,96" fill="var(--offer-red)" stroke="#ffffff" stroke-width="1.5"/>
    </svg>
    <div class="offer-copy">
      <p class="offer-title">INTRODUCTORY OFFER:</p>
      <p class="offer-figure">25% OFF</p>
      <p class="offer-scope">ALL SERVICES</p>
      <p class="offer-refer">REFER A FRIEND: When they book, you will receive 25% OFF your next service!</p>
    </div>
  </div>

  <section class="panel benefits">
    <h2 class="panel-title">DIRECT BENEFITS</h2>
    <div class="benefit-cols">
      <ul class="benefit-list">
        <li>Instantly restores the natural green colour of grass – year round</li>
        <li>Lasts for up to 3 months</li>
        <li>Substantially reduces watering needs</li>
        <li>Pet friendly</li>
        <li>Stays green during droughts and water restrictions</li>
        <li>UV fade resistant</li>
        <li>Won't bleed, run, or stain once absorbed into the grass</li>
      </ul>
      <ul class="benefit-list">
        <li>Safe for the environment, pets and people</li>
        <li>Works in extreme heat, cold and frost</li>
        <li>Organic and natural – no harmful chemicals</li>
        <li>Reduces the amount of fertilizer and water used on lawns</li>
        <li>Kerb appeal is essential for getting your property sold for the high</li>
      </ul>
    </div>
  </section>

  <section class="panel pricing">
    <h2 class="panel-title">SERVICES &amp; PRICING</h2>
    <div class="price-item"><p class="price-name">LAWN MAINTENANCE</p><p class="price-line">Starting from <strong>$60</strong></p></div>
    <div class="price-item"><p class="price-name">LAWN REVIVAL</p><p class="price-line">Starting from <strong>$80</strong></p></div>
    <div class="price-item"><p class="price-name">PACKAGE DEAL</p><p class="price-line">Starting from <strong>$120</strong></p></div>
    <div class="price-item"><p class="price-name">LOCATIONS</p><p class="price-line">Nowra to Sydney</p></div>
  </section>

  <p class="brand">Velvet Turf</p>

  <ul class="contacts">
    <li><span class="contact-chip" aria-hidden="true"></span>hello@velvetturf.example</li>
    <li><span class="contact-chip" aria-hidden="true"></span><span>Chatterbook @velvetturfaus</span></li>
    <li><span class="contact-chip" aria-hidden="true"></span><span>Snapgrid @velvetturfaus</span></li>
  </ul>

  <p class="call">CALL US TODAY <span class="phone">02 5550 1234</span></p>
</main>
</body>
</html>
```